VORTEQ

It’s is a startup business. We design and build new products.

Target Market(s)

For my first two products, they are targeting the laundry market, hanger accessory, and new modern style clothes dryer. I also have a Pet Treat product at patent stage, and there are other products not yet started but will be more engineering based. Therefore from young adults to older population

Industry/Entity Type

Colours of website to match the logo (att)

Coding

Coded - Design and coding required

Number of Pages Required

1 page

Font styles to use
Other font styles liked:
• Some of the same font as the logo

Colors

Designer to choose colors to be used in the design.

Requirements
Must have
• An upbeat vibe - the logo looks great so inline with that !
Should not have
• anything old fashioned and old style fonts

```html
<!DOCTYPE html>
<html lang="en">
<head>
<meta charset="utf-8">
<title>VORTEQ – Innovative Products</title>
<link href="https://fonts.googleapis.com/css2?family=Orbitron:wght@500;700&family=Roboto:wght@400;500;700&family=Roboto+Condensed:wght@700&display=swap" rel="stylesheet">
<style>
:root{
  --navy:#1d2580;
  --navy-deep:#17206b;
  --ink:#13152a;
  --cyan:#14c8d6;
  --cyan-2:#06b2e0;
  --sky:#0a9fd8;
  --hero:#0d3a66;
  --grey:#5b5f6b;
  --white:#ffffff;
  --foot:#12131f;
}
*{box-sizing:border-box;margin:0;padding:0}
html,body{width:1200px;height:3766px;overflow:hidden}
body{position:relative;background:var(--white);font-family:"Roboto",sans-serif;color:var(--grey)}
.abs{position:absolute}
.display{font-family:"Orbitron",sans-serif;font-weight:700;letter-spacing:4px;text-transform:uppercase}
.label{font-family:"Roboto",sans-serif;font-weight:700;color:var(--cyan);font-size:17px}
.btn{position:absolute;display:flex;align-items:center;justify-content:center;border-radius:22px;font-weight:500;font-size:16px;color:var(--white);height:42px}
.btn.cyan{background:var(--cyan)}
.btn.sky{background:var(--cyan-2)}
.btn.navy{background:var(--navy)}

/* header */
.top-line{left:0;top:0;width:1200px;height:3px;background:var(--cyan)}
.brand{display:flex;align-items:center;gap:12px;font-weight:700;color:var(--navy);font-size:40px;letter-spacing:6px}
.brand .dot{width:34px;height:34px;border-radius:50%;background:var(--cyan)}
.social{top:27px;width:45px;height:45px;border:1px solid #dde0ea;border-radius:10px;display:flex;align-items:center;justify-content:center}
.social span{width:12px;height:12px;border-radius:3px;background:var(--navy)}
.call-icon{left:856px;top:25px;width:48px;height:48px;border-radius:10px;background:var(--navy);display:flex;align-items:center;justify-content:center}
.call-small{left:927px;top:28px;font-size:10px;color:#444}
.call-num{left:927px;top:46px;font-size:18px;font-weight:700;color:#222}
.nav-bar{left:0;top:0;z-index:5}
.nav-links{left:0;top:121px;width:1200px;height:20px;z-index:6;font-weight:700;font-size:15px;line-height:20px}
.nav-links a{color:var(--navy);text-decoration:none;position:absolute;top:0;white-space:nowrap}
.nav-links a.active{color:var(--white)}

/* hero */
.hero-title{left:110px;top:296px;font-family:"Roboto Condensed",sans-serif;font-weight:700;font-size:46px;line-height:55px;color:var(--white);letter-spacing:1px}
.hero-sub{left:110px;top:473px;font-size:18px;color:var(--white)}

/* sections */
.center{text-align:center}
.intro{left:190px;width:820px;font-size:15px;line-height:29px;text-align:center;color:var(--grey)}
.card-title{font-weight:700;font-size:20px;color:var(--navy)}
.card-text{font-size:13px;line-height:26px;color:var(--grey);width:330px}
.arrow-tab{width:42px;height:53px;background:var(--cyan-2);display:flex;align-items:center;justify-content:center}

.story-text{left:652px;width:438px;font-size:15px;line-height:30px;color:var(--white);text-align:justify}
.story-text.b{font-weight:500}

.why-card{top:2820px;width:234px;height:263px;border-radius:30px;background:var(--white);box-shadow:0 6px 26px rgba(20,60,120,.08);padding:32px 25px}
.why-card.on{border:1px solid var(--cyan)}
.why-icon{width:86px;height:86px;border-radius:50%;background:var(--cyan);display:flex;align-items:center;justify-content:center}
.why-title{margin-top:25px;font-weight:700;font-size:15px;color:#222}
.why-text{margin-top:8px;font-size:13px;line-height:25px;color:var(--grey)}

.foot-h{top:3480px;font-weight:700;font-size:21px;color:var(--white)}
.foot-list{list-style:none;font-size:14px;color:var(--white)}
.foot-list li{height:33.5px;display:flex;align-items:center;gap:18px}
</style>
</head>
<body>

<!-- header -->
<div class="abs top-line"></div>
<div class="abs brand" style="left:110px;top:36px"><span class="dot"></span>VORTEQ</div>

<div class="abs social" style="left:666px"><span></span></div>
<div class="abs social" style="left:725px"><span></span></div>
<div class="abs social" style="left:784px"><span></span></div>
<div class="abs call-icon">
  <svg width="20" height="20" viewBox="0 0 24 24"><path fill="#fff" d="M6.6 10.8a15 15 0 0 0 6.6 6.6l2.2-2.2c.3-.3.7-.4 1-.2 1.1.4 2.3.6 3.6.6.6 0 1 .4 1 1V20c0 .6-.4 1-1 1A17 17 0 0 1 3 4c0-.6.4-1 1-1h3.5c.6 0 1 .4 1 1 0 1.3.2 2.5.6 3.6.1.3 0 .7-.2 1z"/></svg>
</div>
<div class="abs call-small">CALL US:</div>
<div class="abs call-num">+1 555 014 2290</div>

<!-- hero -->
<svg class="abs" style="left:0;top:127px" width="1200" height="600" viewBox="0 0 1200 600">
  <defs>
    <linearGradient id="herog" x1="0" y1="0" x2="1" y2="1"><stop offset="0" stop-color="#0d4a7c"/><stop offset=".6" stop-color="#0d3560"/><stop offset="1" stop-color="#0a2a52"/></linearGradient>
    <radialGradient id="glow" cx=".72" cy=".27" r=".45"><stop offset="0" stop-color="#7fd8ff" stop-opacity=".55"/><stop offset="1" stop-color="#0d3a66" stop-opacity="0"/></radialGradient>
  </defs>
  <polygon points="0,463 330,593 1200,418 1200,0 0,0" fill="#16c0e0"/>
  <polygon points="0,463 330,560 1200,415 1200,0 0,0" fill="url(#herog)"/>
  <rect x="520" y="60" width="680" height="460" fill="url(#glow)" role="img" aria-label="Hand reaching toward a glowing digital wireframe hand"/>
</svg>

<!-- navigation (above hero) -->
<svg class="abs nav-bar" width="1200" height="170" viewBox="0 0 1200 170">
  <defs><linearGradient id="navg" x1="0" x2="1"><stop offset="0" stop-color="#0cb6e6"/><stop offset="1" stop-color="#16cde0"/></linearGradient></defs>
  <polygon points="535,96 1200,96 1200,165 535,165 518,130" fill="url(#navg)"/>
</svg>
<nav class="abs nav-links">
  <a class="active" href="#" style="left:570px">HOME</a>
  <a href="#" style="left:650px">ABOUT US</a>
  <a href="#" style="left:757px">INNOVATIONS</a>
  <a href="#" style="left:889px">PRODUCTS</a>
  <a href="#" style="left:1001px">CONTACT US</a>
</nav>

<h1 class="abs hero-title">INNOVATIVE PRODUCTS<br>FOR YOUR EVERYDAY<br>LIFE</h1>
<p class="abs hero-sub">Designing smarter solutions for laundry, pets, &amp; beyond.</p>
<a class="btn cyan" style="left:110px;top:516px;width:180px">See What's New</a>
<a class="btn sky" style="left:307px;top:516px;width:216px">Explore Our Products</a>

<!-- featured -->
<div class="abs label" style="left:440px;top:818px">FEATURED PRODUCTS</div>
<div class="abs display" style="left:440px;top:845px;font-size:22px;color:var(--navy)">Our Innovations</div>
<p class="abs intro" style="top:896px">Sed ut perspiciatis unde omnis iste natus error sit voluptatem accusantium doloremque laudantium, totam rem aperiam, eaque ipsa quae ab illo inventore veritatis et quasi architecto beatae vitae dicta sunt</p>

<div class="abs" role="img" aria-label="Laundry shelves with folded towels and baskets" style="left:110px;top:983px;width:474px;height:332px;background:linear-gradient(180deg,#e9e6df,#c9c6bf 70%,#a9a7a2)"></div>
<svg class="abs" style="left:138px;top:1218px" width="420" height="235" viewBox="0 0 420 235"><polygon points="0,0 365,0 415,232 0,232" fill="#fff" style="filter:drop-shadow(0 8px 18px rgba(20,40,90,.08))"/></svg>
<div class="abs arrow-tab" style="left:543px;top:1262px"><svg width="14" height="14" viewBox="0 0 14 14"><path d="M2 7h9M7 3l4 4-4 4" stroke="#fff" stroke-width="2.4" fill="none"/></svg></div>
<svg class="abs" style="left:180px;top:1243px" width="68" height="68" viewBox="0 0 68 68"><rect x="4" y="4" width="60" height="60" rx="12" fill="#e6ebf6"/><rect x="16" y="14" width="34" height="40" rx="5" fill="var(--navy)"/><circle cx="33" cy="38" r="10" fill="#fff"/><rect x="38" y="34" width="18" height="14" rx="3" fill="#2fb1e8"/></svg>
<div class="abs card-title" style="left:180px;top:1325px">LAUNDRY ACCESSORIES</div>
<p class="abs card-text" style="left:180px;top:1357px">Sed ut perspiciatis unde omnis iste natus error sit voluptatem accusantium doloremque laudantium, totam rem aperiam, eaque ipsa</p>

<div class="abs" role="img" aria-label="Modern washer and dryer in a bright laundry room" style="left:615px;top:983px;width:474px;height:332px;background:linear-gradient(135deg,#5b6b3a,#a69a7c 45%,#d8d3c6 70%,#8a6a3e)"></div>
<svg class="abs" style="left:640px;top:1218px" width="440" height="248" viewBox="0 0 440 248"><polygon points="0,0 355,0 440,246 20,246 20,232 0,232" fill="var(--cyan)"/><polygon points="2,0 355,0 420,232 2,232" fill="#fff"/></svg>
<div class="abs arrow-tab" style="left:1047px;top:1262px"><svg width="14" height="14" viewBox="0 0 14 14"><path d="M2 7h9M7 3l4 4-4 4" stroke="#fff" stroke-width="2.4" fill="none"/></svg></div>
<svg class="abs" style="left:682px;top:1243px" width="68" height="68" viewBox="0 0 68 68"><rect x="10" y="4" width="48" height="60" rx="9" fill="var(--navy)"/><circle cx="34" cy="40" r="15" fill="#fff"/><circle cx="34" cy="40" r="6" fill="#2fb1e8"/><rect x="18" y="11" width="32" height="4" rx="2" fill="#2fb1e8"/></svg>
<div class="abs card-title" style="left:682px;top:1325px">CLOTHES DRYER</div>
<p class="abs card-text" style="left:682px;top:1357px">Sed ut perspiciatis unde omnis iste natus error sit voluptatem accusantium doloremque laudantium, totam rem aperiam, eaque ipsa</p>

<!-- story -->
<svg class="abs" style="left:0;top:1545px" width="1200" height="725" viewBox="0 0 1200 725">
  <defs><linearGradient id="storyg" x1="0" y1="0" x2="1" y2="1"><stop offset="0" stop-color="#12c9d8"/><stop offset=".5" stop-color="#0aa9dc"/><stop offset="1" stop-color="#0a8fd6"/></linearGradient></defs>
  <polygon points="0,130 870,0 1200,130 1200,725 0,725" fill="var(--navy)"/>
  <polygon points="0,130 870,25 1200,150 1200,725 0,725" fill="url(#storyg)"/>
</svg>
<div class="abs" role="img" aria-label="Glowing light bulb with network lines over a team working at a desk" style="left:0;top:1706px;width:586px;height:494px;background:radial-gradient(circle at 52% 48%,#f6a23a 0,#b45a16 14%,#3a3f55 40%,#1f2638 100%)"></div>
<div class="abs label" style="left:727px;top:1743px;color:var(--white)">OUR STORY</div>
<div class="abs display" style="left:727px;top:1773px;font-size:22px;line-height:37px;color:var(--white)">From Idea To<br>Innovation</div>
<p class="abs story-text b" style="top:1866px">Sed ut perspiciatis unde omnis iste natus error sit voluptatem accusantium doloremque laudantium, totam rem aperiam, eaque ipsa quae ab illo inventore veritatis et quasi architecto beatae vitae dicta sunt explicabo. Nemo enim ipsam voluptatem quia voluptas sit aspernatur aut odit aut fugit</p>
<p class="abs story-text b" style="top:2030px">Totam rem aperiam, eaque ipsa quae ab illo inventore veritatis et quasi architecto beatae vitae dicta sunt explicabo.</p>
<a class="btn navy" style="left:652px;top:2115px;width:156px">Explore More</a>

<!-- join -->
<div class="abs" style="left:0;top:2270px;width:1200px;height:352px;background:linear-gradient(160deg,#1d2a8a,#1a2478 60%,#16206b)"></div>
<div class="abs label" style="left:261px;top:2332px">JOIN WITH US</div>
<div class="abs display" style="left:261px;top:2360px;font-size:22px;color:var(--white)">Ready To Improve Your Life?</div>
<p class="abs intro" style="top:2410px;color:var(--white);font-weight:500">Sed ut perspiciatis unde omnis iste natus error sit voluptatem accusantium doloremque laudantium, totam rem aperiam, eaque ipsa quae ab illo inventore veritatis et quasi architecto beatae vitae dicta sunt</p>
<p class="abs center" style="left:0;width:1200px;top:2480px;font-size:15px;font-weight:500;color:var(--cyan)">Quis autem vel eum iure reprehenderit qui in ea voluptate velit esse</p>
<a class="btn cyan" style="left:423px;top:2522px;width:180px">See What's New</a>
<a class="btn sky" style="left:622px;top:2522px;width:155px">Get In Touch</a>

<!-- why choose -->
<div class="abs label" style="left:385px;top:2713px">OUR PRODUCTS ARE DESIGNED TO MAKE YOUR LIFE EASIER</div>
<div class="abs display" style="left:385px;top:2741px;font-size:22px;color:var(--navy)">Why Choose Us?</div>

<div class="abs why-card" style="left:110px">
  <div class="why-icon"><svg width="44" height="44" viewBox="0 0 44 44"><path d="M22 38 6 22a9 9 0 0 1 16-10 9 9 0 0 1 16 10z" fill="#fff"/></svg></div>
  <div class="why-title">SPACE-SAVING</div>
  <p class="why-text">Quis autem vel eum iure repr ehenderit qui in ea voluptate velit esse</p>
</div>
<div class="abs why-card on" style="left:358px">
  <div class="why-icon"><svg width="44" height="44" viewBox="0 0 44 44"><circle cx="22" cy="22" r="14" fill="none" stroke="#fff" stroke-width="5"/><path d="M24 8 16 24h8l-4 12 10-17h-8z" fill="#fff"/></svg></div>
  <div class="why-title">ENERGY-EFFICIENT</div>
  <p class="why-text">Quis autem vel eum iure repr ehenderit qui in ea voluptate velit esse</p>
</div>
<div class="abs why-card" style="left:606px">
  <div class="why-icon"><svg width="44" height="44" viewBox="0 0 44 44"><path d="M20 5 6 10v10c0 9 6 15 14 18 8-3 14-9 14-18V10z" fill="#fff"/><circle cx="32" cy="32" r="8" fill="var(--navy)"/><path d="m28 32 3 3 5-6" stroke="#fff" stroke-width="2" fill="none"/></svg></div>
  <div class="why-title">DURABLE</div>
  <p class="why-text">Quis autem vel eum iure repr ehenderit qui in ea voluptate velit esse</p>
</div>
<div class="abs why-card" style="left:854px">
  <div class="why-icon"><svg width="44" height="44" viewBox="0 0 44 44"><path d="M22 6a16 16 0 1 0 16 16" fill="none" stroke="#fff" stroke-width="5"/><path d="M34 6c-10 0-16 6-16 16 10 0 16-6 16-16z" fill="#fff"/></svg></div>
  <div class="why-title">ECO-FRIENDLY</div>
  <p class="why-text">Quis autem vel eum iure repr ehenderit qui in ea voluptate velit esse</p>
</div>
<a class="btn navy" style="left:522px;top:3127px;width:156px">Explore More</a>

<!-- footer -->
<svg class="abs" style="left:0;top:3220px" width="1200" height="546" viewBox="0 0 1200 546">
  <polygon points="0,165 870,0 1200,125 1200,546 0,546" fill="var(--cyan)"/>
  <polygon points="0,175 870,30 1200,150 1200,546 0,546" fill="var(--foot)"/>
</svg>
<div class="abs brand" style="left:640px;top:3335px;font-size:64px;letter-spacing:12px;color:var(--white)"><span class="dot" style="width:56px;height:56px"></span>VORTEQ</div>

<div class="abs foot-h" style="left:110px">QUICK LINKS</div>
<ul class="abs foot-list" style="left:110px;top:3512px">
  <li><span>»</span>Home</li><li><span>»</span>About Us</li><li><span>»</span>Our Innovations</li><li><span>»</span>Why Choose Us?</li><li><span>»</span>Contact Us</li>
</ul>
<div class="abs foot-h" style="left:349px">CONTACT US</div>
<ul class="abs foot-list" style="left:349px;top:3512px">
  <li><svg width="12" height="14" viewBox="0 0 12 14"><path d="M6 0a5 5 0 0 0-5 5c0 4 5 9 5 9s5-5 5-9a5 5 0 0 0-5-5zm0 7a2 2 0 1 1 0-4 2 2 0 0 1 0 4z" fill="#fff"/></svg>14B, Vorteq Innovation &amp; Technical Services</li>
  <li style="padding-left:30px">210457</li>
  <li><svg width="12" height="12" viewBox="0 0 24 24"><path fill="#fff" d="M6.6 10.8a15 15 0 0 0 6.6 6.6l2.2-2.2c.3-.3.7-.4 1-.2 1.1.4 2.3.6 3.6.6.6 0 1 .4 1 1V20c0 .6-.4 1-1 1A17 17 0 0 1 3 4c0-.6.4-1 1-1h3.5c.6 0 1 .4 1 1 0 1.3.2 2.5.6 3.6.1.3 0 .7-.2 1z"/></svg>+1 555 014 2290</li>
  <li><svg width="12" height="10" viewBox="0 0 12 10"><rect width="12" height="10" rx="1" fill="#fff"/><path d="m0 1 6 4 6-4" stroke="#12131f" fill="none"/></svg>info@vorteqstudio.com</li>
  <li><svg width="12" height="12" viewBox="0 0 12 12"><circle cx="6" cy="6" r="5.5" fill="#fff"/><path d="M1 6h10M6 1c-2 3-2 7 0 10M6 1c2 3 2 7 0 10" stroke="#12131f" fill="none" stroke-width=".8"/></svg>www.vorteq-labs.com</li>
</ul>
<div class="abs foot-h" style="left:727px">SUBSCRIBE FOR UPDATES</div>
<div class="abs" style="left:728px;top:3525px;width:202px;height:44px;border-radius:22px;background:#fff;font-size:12px;color:#555;display:flex;align-items:center;padding-left:24px">Email Address</div>
<a class="btn cyan" style="left:946px;top:3525px;width:142px;height:44px;color:var(--navy)">Subscribe</a>
<div class="abs" style="left:110px;top:3715px;width:980px;height:1px;background:#2c2e3e"></div>
<p class="abs center" style="left:0;width:1200px;top:3736px;font-size:10px;color:#fff">(C) Copyright | All Rights Reserved</p>

</body>
</html>
```